design a construction company business card

Design business card around our logo. Card must have all the typical info: name, title, address, phone, email, business name, etc. Somewhere on the card I would like to see our motto "Solid work... Steady hands, honest hearts." Consider adding a splash of bright orange to the card to complement the blues and silvers/grays in the logo. We are open to metallic inks, textures, etc. We would like to see options on both light and dark backgrounds. The font in the logo is Euro Technic Extended Regular.

```html
<!DOCTYPE html>
<html lang="en">
<head>
<meta charset="utf-8">
<title>Halden Contracting – Business Card</title>
<link href="https://fonts.googleapis.com/css2?family=Roboto:ital,wght@0,400;0,500;1,400&display=swap" rel="stylesheet">
<style>
  :root {
    --blue-deep: #2a4aa8;
    --blue-mid: #2f62bd;
    --blue-light: #3079c4;
    --orange: #f08a1c;
    --white: #ffffff;
    --ink: #111111;
    --backdrop: #e6e7ea;
  }
  html, body {
    margin: 0;
    width: 1200px;
    height: 1200px;
    overflow: hidden;
    background: var(--backdrop);
    font-family: "Roboto", Arial, sans-serif;
  }
  .canvas {
    width: 1200px;
    height: 1200px;
    display: flex;
    flex-direction: column;
    align-items: center;
    justify-content: center;
    gap: 60px;
  }
  .card {
    position: relative;
    width: 840px;
    height: 480px;
    overflow: hidden;
    box-shadow: 0 6px 20px rgba(0,0,0,0.18);
  }
  /* Front */
  .card-front { background: var(--white); }
  .front-shapes { position: absolute; inset: 0; }
  .wordmark {
    display: flex;
    align-items: center;
    gap: 12px;
    font-weight: 500;
    letter-spacing: 1px;
    margin: 0;
  }
  .wordmark-square { width: 18px; height: 18px; flex: none; }
  .card-front .wordmark {
    position: absolute;
    left: 48px;
    top: 62px;
    color: var(--blue-deep);
    font-size: 30px;
  }
  .card-front .wordmark-square { background: var(--blue-deep); }
  .holder {
    position: absolute;
    right: 60px;
    top: 120px;
    text-align right;
    text-align: right;
  }
  .holder-name { font-size: 46px; color: var(--ink); font-weight: 400; margin: 0; }
  .holder-title { font-size: 20px; letter-spacing: 2px; color: var(--ink); margin: 6px 0 0; }
  .contact {
    position: absolute;
    left: 340px;
    top: 290px;
    color: var(--white);
    font-size: 19px;
    line-height: 1.55;
  }
  .contact-row { display: flex; align-items: center; gap: 16px; }
  .contact-icons { position: absolute; left: 250px; top: 286px; }
  .website {
    position: absolute;
    left: 40px;
    bottom: 34px;
    color: var(--white);
    font-size: 19px;
  }
  /* Back */
  .card-back {
    background: linear-gradient(120deg, var(--blue-deep) 0%, var(--blue-mid) 55%, var(--blue-light) 100%);
  }
  .motto {
    position: absolute;
    left: 48px;
    top: 40px;
    margin: 0;
    color: var(--white);
    font-size: 24px;
    font-style: italic;
    letter-spacing: 0.5px;
  }
  .card-back .wordmark {
    position: absolute;
    left: 0; right: 0; top: 210px;
    justify-content: center;
    color: var(--white);
    font-size: 44px;
  }
  .card-back .wordmark-square { width: 26px; height: 26px; background: var(--white); }
</style>
</head>
<body>
<main class="canvas">
  <section class="card card-front" aria-label="Business card front">
    <svg class="front-shapes" width="840" height="480" viewBox="0 0 840 480">
      <polyline points="0,168 226,168 300,242 840,242" fill="none" stroke="var(--orange)" stroke-width="7"/>
      <polygon points="0,190 220,190 300,270 840,270 840,480 0,480" fill="var(--blue-mid)"/>
    </svg>

    <p class="wordmark"><span class="wordmark-square"></span>Halden Contracting, Inc.</p>

    <div class="holder">
      <p class="holder-name">Marcus Reed</p>
      <p class="holder-title">CONTRACTOR</p>
    </div>

    <svg class="contact-icons" width="70" height="130" viewBox="0 0 70 130" aria-hidden="true">
      <line x1="52" y1="20" x2="20" y2="105" stroke="var(--white)" stroke-width="2"/>
      <circle cx="52" cy="20" r="15" fill="var(--blue-mid)" stroke="var(--white)" stroke-width="2"/>
      <path d="M52 12 a6 6 0 0 1 6 6 c0 5 -6 11 -6 11 s-6 -6 -6 -11 a6 6 0 0 1 6 -6z" fill="var(--white)"/>
      <circle cx="36" cy="62" r="15" fill="var(--blue-mid)" stroke="var(--white)" stroke-width="2"/>
      <path d="M30 56 l4 0 l2 4 l-2 2 a9 9 0 0 0 4 4 l2 -2 l4 2 l0 4 a2 2 0 0 1 -2 2 a14 14 0 0 1 -14 -14 a2 2 0 0 1 2 -2z" fill="var(--white)"/>
      <circle cx="20" cy="105" r="15" fill="var(--blue-mid)" stroke="var(--white)" stroke-width="2"/>
      <rect x="12" y="99" width="16" height="12" fill="none" stroke="var(--white)" stroke-width="2"/>
      <polyline points="12,99 20,106 28,99" fill="none" stroke="var(--white)" stroke-width="2"/>
    </svg>

    <div class="contact">
      <div class="contact-row">4120 Birchmont Ave. Dayton, OH 45402</div>
      <div class="contact-row">555-014-2236</div>
      <div class="contact-row">mreed@haldencontracting.com</div>
    </div>

    <div class="website">www.haldencontracting.com</div>
  </section>

  <section class="card card-back" aria-label="Business card back">
    <p class="motto">“Solid work... Steady hands, honest hearts.”</p>
    <p class="wordmark"><span class="wordmark-square"></span>Halden Contracting, Inc.</p>
  </section>
</main>
</body>
</html>
```